Business Cards for a law firm

Business cards for our law firm. Use our silhoette logo and OAK PARTNERS - check our website (www.oakpartners.example)

Contact Information for Business Card

our silhouette logo, OAK PARTNERS, 800-555-0147, Dorian Pemberton, dorian@oakpartners.example

Requirements
Must have
• our silhouette logo, OAK PARTNERS, 800-555-0147, Dorian Pemberton, dorian@oakpartners.example

```html
<!DOCTYPE html>
<html lang="en">
<head>
<meta charset="utf-8">
<title>Oak Partners – Business Card</title>
<link href="https://fonts.googleapis.com/css2?family=Montserrat:wght@400;500;700&display=swap" rel="stylesheet">
<style>
  :root {
    --page-bg: #e9e9eb;
    --card-white: #ffffff;
    --navy: #27306e;
    --navy-deep: #1f2a62;
    --pattern-light: #4161ad;
    --pattern-dark: #1c255a;
    --ink: #1d1d24;
    --white: #ffffff;
  }
  * { margin: 0; padding: 0; box-sizing: border-box; }
  html, body {
    width: 1200px;
    height: 1108px;
    overflow: hidden;
    background: var(--page-bg);
    font-family: "Montserrat", sans-serif;
  }
  .card {
    position: absolute;
    left: 212px;
    width: 776px;
  }
  .card--front {
    top: 50px;
    height: 473px;
    background: var(--card-white);
  }
  .card--back {
    top: 568px;
    height: 457px;
    background: var(--navy-deep);
    overflow: hidden;
  }

  /* Front */
  .front-brand {
    position: absolute;
    left: 98px;
    top: 254px;
    font-weight: 500;
    font-size: 21px;
    letter-spacing: 2.6px;
    color: var(--navy);
  }
  .front-divider {
    position: absolute;
    left: 387px;
    top: 185px;
    width: 2px;
    height: 158px;
    background: var(--navy);
  }
  .contact {
    position: absolute;
    left: 401px;
    top: 184px;
    color: var(--ink);
  }
  .contact__name {
    font-weight: 700;
    font-size: 29px;
    color: var(--navy);
    letter-spacing: -0.2px;
    line-height: 36px;
  }
  .contact__role {
    font-size: 17px;
    line-height: 24px;
    margin-bottom: 8px;
  }
  .contact__list { list-style: none; }
  .contact__item {
    display: flex;
    align-items: center;
    font-size: 17.5px;
    line-height: 30.5px;
  }
  .contact__icon {
    width: 17px;
    height: 17px;
    margin-right: 9px;
    fill: var(--navy);
    flex: none;
  }

  /* Back */
  .back-pattern {
    position: absolute;
    inset: 0;
    background: linear-gradient(100deg, var(--pattern-light) 0%, #30469a 30%, #23306e 55%, var(--pattern-dark) 100%);
    opacity: 0.85;
  }
  .back-brand {
    position: absolute;
    left: 0;
    right: 0;
    top: 300px;
    text-align: center;
    padding-left: 80px;
    font-weight: 500;
    font-size: 31px;
    letter-spacing: 3.8px;
    color: var(--white);
  }
</style>
</head>
<body>
  <section class="card card--front">
    <div class="front-brand">OAK PARTNERS</div>
    <div class="front-divider"></div>
    <div class="contact">
      <div class="contact__name">Dorian Pemberton</div>
      <div class="contact__role">Lawyer</div>
      <ul class="contact__list">
        <li class="contact__item">
          <svg class="contact__icon" viewBox="0 0 24 24" aria-hidden="true"><path d="M6.6 10.8a15.1 15.1 0 0 0 6.6 6.6l2.2-2.2c.3-.3.7-.4 1-.2 1.1.4 2.3.6 3.6.6.6 0 1 .4 1 1V20c0 .6-.4 1-1 1A17 17 0 0 1 3 4c0-.6.4-1 1-1h3.5c.6 0 1 .4 1 1 0 1.3.2 2.5.6 3.6.1.3 0 .7-.2 1z"/></svg>
          800-555-0147
        </li>
        <li class="contact__item">
          <svg class="contact__icon" viewBox="0 0 24 24" aria-hidden="true"><path d="M3 6h18v12H3z" opacity=".0"/><path d="M3 6.5h18v1.2l-9 5.6-9-5.6zM3 9.6l9 5.6 9-5.6V18H3z"/></svg>
          dorian@oakpartners.example
        </li>
        <li class="contact__item">
          <svg class="contact__icon" viewBox="0 0 24 24" aria-hidden="true"><path d="M12 2a10 10 0 1 0 0 20 10 10 0 0 0 0-20zm-1 17.9A8 8 0 0 1 4.2 10.2L9 15v1a2 2 0 0 0 2 2zm6.9-2.5A2 2 0 0 0 16 16h-1v-3a1 1 0 0 0-1-1H8v-2h2a1 1 0 0 0 1-1V7h2a2 2 0 0 0 2-2v-.4a8 8 0 0 1 2.9 12.8z"/></svg>
          www.oakpartners.example
        </li>
      </ul>
    </div>
  </section>

  <section class="card card--back">
    <div class="back-pattern" role="img" aria-label="Repeating pattern of the firm's silhouette mark fading from light blue to navy"></div>
    <div class="back-brand">OAK PARTNERS</div>
  </section>
</body>
</html>
```